KAJU Freightways #ALLKAJU Business Cards & Letterhead

I am looking to business cards designed for our organization. We are currently undergoing a small re-branding that is taking place. Our organization is called KAJU Freightways and we are headquartered in Phoenix, AZ. We primarily provide transportation and logistics services to the Marlow Parcel Bureau who is our largest customer. I would like to see a design that incorporates name, title, contact info, website, and address (this will be different depending on the employee). I would also like to see some color on the business card using our logo colors or a variation. I would like our logo on the back of the business card with the website displayed. The final design should communicate that we are a next generation transportation operate that focuses on being driver-first, customer-centric, innovative, and sustainable.We would also like our #ALLKAJU catch phrase incorporated as well.

Target Market(s)

Transportation & Logistics

Industry/Entity Type

Trucking Company

Contact Information for Business Card

-First and Last Name
-Position Title
-Contact Phone
-Contact Email
-Physical Address

Font styles to use
Serif

Colors

Designer to choose colors to be used in the design.

Requirements
Must have
• -KAJU logo prominently displayed
• -#ALLKAJU catch phrase used
• -Some amount of color, design gradient, etc.
• -Logo on the back with website listed (https://www.kajufreightco.example)

```html
<!DOCTYPE html>
<html lang="en">
<head>
<meta charset="utf-8">
<title>KAJU Freightways Business Card</title>
<link href="https://fonts.googleapis.com/css2?family=Montserrat:wght@300;400;600;700;800&display=swap" rel="stylesheet">
<style>
  :root {
    --teal-deep: #0d3340;
    --teal: #13404f;
    --green: #7cc242;
    --white: #ffffff;
    --muted: #9aa9b0;
    --backdrop: #2a2d31;
  }
  html, body {
    margin: 0;
    padding: 0;
    width: 1200px;
    height: 900px;
    overflow: hidden;
    background: var(--backdrop);
    font-family: "Montserrat", sans-serif;
  }
  .sheet {
    width: 1200px;
    height: 900px;
    display: flex;
    flex-direction: column;
    align-items: center;
    justify-content: center;
    gap: 40px;
  }
  .card {
    position: relative;
    width: 700px;
    height: 400px;
    overflow: hidden;
    box-shadow: 0 12px 30px rgba(0,0,0,0.45);
  }
  .card-front { background: var(--white); }
  .front-shapes { position: absolute; inset: 0; }

  .front-brand {
    position: absolute;
    left: 60px;
    top: 70px;
    display: flex;
    align-items: center;
    gap: 14px;
  }
  .brand-name {
    font-weight: 800;
    font-size: 64px;
    letter-spacing: 2px;
    color: var(--teal-deep);
    line-height: 1;
  }
  .brand-dot {
    width: 22px;
    height: 22px;
    border-radius: 50%;
    background: var(--green);
  }

  .contact {
    position: absolute;
    right: 40px;
    top: 178px;
    text-align: right;
    color: var(--white);
  }
  .contact-name {
    font-weight: 700;
    font-size: 26px;
    letter-spacing: 1px;
    margin: 0;
    line-height: 1.1;
  }
  .contact-title {
    font-weight: 400;
    font-size: 17px;
    margin: 2px 0 14px;
  }
  .contact-address {
    font-weight: 400;
    font-size: 15px;
    color: var(--muted);
    line-height: 1.35;
    margin: 0 0 10px;
  }
  .contact-line {
    display: flex;
    justify-content: flex-end;
    align-items: center;
    gap: 8px;
    font-size: 15px;
    color: var(--muted);
    line-height: 1.5;
  }
  .contact-line svg { width: 15px; height: 15px; flex: none; }
  .web-strong { color: var(--green); font-weight: 700; }

  .card-back {
    background: linear-gradient(160deg, #164656 0%, var(--teal-deep) 100%);
    color: var(--white);
  }
  .back-rule {
    position: absolute;
    left: 0;
    right: 0;
    top: 92px;
    height: 1px;
    background: var(--green);
    opacity: 0.7;
  }
  .back-brand {
    position: absolute;
    left: 0;
    right: 0;
    top: 120px;
    text-align: center;
  }
  .back-name {
    font-weight: 800;
    font-size: 88px;
    letter-spacing: 4px;
    line-height: 1;
    margin: 0;
  }
  .back-sub {
    font-weight: 600;
    font-size: 20px;
    letter-spacing: 3px;
    margin: 10px 0 6px;
  }
  .back-tag {
    display: flex;
    align-items: center;
    justify-content: center;
    gap: 10px;
    color: var(--green);
    font-size: 15px;
    letter-spacing: 1px;
    font-weight: 400;
  }
  .back-tag::before,
  .back-tag::after {
    content: "";
    width: 60px;
    height: 1px;
    background: var(--green);
  }
  .back-web {
    font-size: 17px;
    margin-top: 6px;
    font-weight: 300;
  }
</style>
</head>
<body>
<main class="sheet">

  <section class="card card-front" aria-label="Business card front">
    <svg class="front-shapes" viewBox="0 0 700 400" preserveAspectRatio="none" aria-hidden="true">
      <path d="M0,150 C140,200 300,200 420,205 C300,215 150,205 0,170 Z" fill="var(--green)"/>
      <path d="M0,178 C160,250 380,228 500,152 C590,100 660,40 700,-10 L700,400 L0,400 Z" fill="var(--green)"/>
      <path d="M0,200 C160,268 385,248 505,172 C595,118 665,58 700,22 L700,400 L0,400 Z" fill="var(--teal)"/>
    </svg>

    <div class="front-brand">
      <span class="brand-name">KAJU</span>
      <span class="brand-dot"></span>
    </div>

    <div class="contact">
      <p class="contact-name">DANA REYES</p>
      <p class="contact-title">Chairman &amp; CEO</p>
      <p class="contact-address">4170 North Cactus Ridge<br>Drive, Peoria, AZ 85390</p>
      <div class="contact-line">623-555-0148
        <svg viewBox="0 0 16 16"><circle cx="8" cy="8" r="7" fill="none" stroke="var(--green)" stroke-width="1.4"/><path d="M5.5 4.5l1.5 0 .6 2-1 .8c.5 1 1.2 1.7 2.2 2.2l.8-1 2 .6v1.5c-3.5.3-6.4-2.6-6.1-6.1z" fill="var(--green)"/></svg>
      </div>
      <div class="contact-line">info@kajufreightco.example
        <svg viewBox="0 0 16 16"><rect x="1.5" y="3.5" width="13" height="9" fill="none" stroke="var(--green)" stroke-width="1.4"/><path d="M1.5 3.5l6.5 5 6.5-5" fill="none" stroke="var(--green)" stroke-width="1.4"/></svg>
      </div>
      <div class="contact-line"><span>www.<span class="web-strong">kajufreightco</span>.example</span>
        <svg viewBox="0 0 16 16"><circle cx="8" cy="8" r="7" fill="var(--green)"/><path d="M1 8h14M8 1c-3 3-3 11 0 14M8 1c3 3 3 11 0 14" fill="none" stroke="var(--teal)" stroke-width="1"/></svg>
      </div>
    </div>
  </section>

  <section class="card card-back" aria-label="Business card back">
    <div class="back-rule"></div>
    <div class="back-brand">
      <p class="back-name">KAJU</p>
      <p class="back-sub">FREIGHTWAYS</p>
      <div class="back-tag">#ALLKAJU</div>
      <div class="back-web">www.<span class="web-strong">kajufreightco</span>.example</div>
    </div>
  </section>

</main>
</body>
</html>
```